Pawn & Gun store business card design

Hello! We would like a new business card design for our pawn & gun store. We loan money on items of value and sell firearms, jewelry, electronics & more.

Card will need to have the following information:

Business name - Prairie Nickel Pawn & Gun
Address - 2417 Hwy 53 S. Suite C Harlan Flats, KS 75246
Employees name - Darren Kellum
Phone number - 555-613-8840
Email - PrairieNickelPawn@Mailvera.com
Website - PrairieNickelPawn.com

Somewhere on the card we would like it to say "Offering 10 Month Layaway!" & "We buy & loan on anything of value!". Our main store color is orange (please see logo). Logo does not have to be on the business card but it can be. Would like the back to have an area to write a note on the back. We like vintage things like old coins, collectables, firearms and more so think about this in the design. We want a business card as unique as our store!

Colors

Designer to choose colors to be used in the design.

Requirements
Nice to have
• Vintage Style

```html
<!DOCTYPE html>
<html lang="en">
<head>
<meta charset="utf-8">
<title>Prairie Nickel Pawn &amp; Gun — Business Card</title>
<link href="https://fonts.googleapis.com/css2?family=Arvo:wght@700&family=Roboto:wght@400&family=EB+Garamond:ital,wght@0,700;1,400&display=swap" rel="stylesheet">
<style>
  :root {
    --bg: #ece4dc;
    --paper: #fbfbfa;
    --orange: #d2601a;
    --brown: #3b2418;
    --ink: #4a4a4a;
    --rule: #6b6b6b;
  }
  * { margin: 0; padding: 0; box-sizing: border-box; }
  html, body {
    width: 1200px; height: 974px; overflow: hidden;
    background: var(--bg);
  }
  .canvas {
    position: relative; width: 1200px; height: 974px;
  }
  .card {
    position: absolute; top: 167px;
    width: 380px; height: 640px;
    background: var(--paper);
    box-shadow: 0 6px 18px rgba(60, 40, 20, 0.18);
  }
  .card--front { left: 190px; }
  .card--back { left: 630px; }

  .brand {
    position: absolute; left: 40px; top: 56px;
    display: flex; align-items: center; gap: 12px;
  }
  .brand__dot {
    width: 22px; height: 22px; border-radius: 50%;
    background: var(--orange);
  }
  .brand__name {
    font-family: "Arvo", serif; font-weight: 700;
    font-size: 26px; line-height: 1.1;
    color: var(--orange);
  }

  .holder {
    position: absolute; left: 40px; top: 300px;
    font-family: "Arvo", serif; font-weight: 700;
    font-size: 38px; color: var(--orange);
    white-space: nowrap;
  }
  .divider {
    position: absolute; left: 40px; top: 366px;
    width: 96px; border-top: 2px dotted var(--rule);
  }
  .contact {
    position: absolute; left: 40px; top: 392px;
    font-family: "Roboto", sans-serif; font-size: 19px;
    line-height: 27px; color: var(--ink);
    white-space: nowrap;
  }
  .contact__lines { margin-bottom: 14px; }
  .website {
    position: absolute; left: 40px; top: 566px;
    font-family: "Roboto", sans-serif; font-size: 19px;
    color: var(--orange);
  }

  .note-area {
    position: absolute; left: 30px; right: 30px; top: 30px; bottom: 140px;
  }
  .offer {
    position: absolute; left: 0; right: 0; bottom: 70px;
    text-align: center;
  }
  .offer__headline {
    font-family: "EB Garamond", serif; font-weight: 700;
    font-size: 21px; letter-spacing: 0.5px;
    color: var(--brown); text-transform: uppercase;
  }
  .offer__tagline {
    display: flex; align-items: center; justify-content: center; gap: 8px;
    margin-top: 2px;
    font-family: "EB Garamond", serif; font-style: italic;
    font-size: 16px; color: var(--orange);
  }
  .offer__tagline::before, .offer__tagline::after {
    content: ""; width: 38px; border-top: 1px solid var(--brown);
  }
</style>
</head>
<body>
<main class="canvas">
  <section class="card card--front" aria-label="Card front">
    <div class="brand">
      <span class="brand__dot"></span>
      <span class="brand__name">Prairie Nickel<br>Pawn</span>
    </div>
    <h1 class="holder">Darren Kellum</h1>
    <div class="divider"></div>
    <div class="contact">
      <p class="contact__lines">Prairie Nickel Pawn &amp; Gun<br>2417 Hwy 53 S.<br>Suite C Harlan Flats, KS 75246</p>
      <p>P. 555-613-8840<br>PrairieNickelPawn@Mailvera.com</p>
    </div>
    <p class="website">www.PrairieNickelPawn.com</p>
  </section>

  <section class="card card--back" aria-label="Card back">
    <div class="note-area" aria-label="Space for a handwritten note"></div>
    <div class="offer">
      <p class="offer__headline">Offering 10 Month Layaway</p>
      <p class="offer__tagline">We buy &amp; loan on anything of value</p>
    </div>
  </section>
</main>
</body>
</html>
```